Bright Harbor website redesign

We need a redesign for a website: mybrightharbor.example.

I already created a video going over what exactly is needed in the design.

See Video here: https://files.example.net/file/d/7xQpL2mR9vTz4KwB8nYcH3jDs6FgA1eU0/view?usp=sharing

ReviewHub Slide shown in Video: https://slides.example.net/presentation/d/9KP_Rtnwq3XbzmLeYc7VhJ2GoUd4Fs_PaiTe6q1kQ5Wr/edit?usp=sharing

Holidays in India so we did not get enough design entries or quality.

Target Market(s)

Dentistry

Industry/Entity Type

Dentistry

Number of Pages Required

1 page

Colors
0094D4
00A9DD
6FCCEA
C7EBF8
E9F6FB
00AB8E
00BBA5
67D7C9
C6EFE9
E9F9F6

Requirements
Must have
• See 13 min video link in description - shows what to do.

```html
<!DOCTYPE html>
<html lang="en">
<head>
<meta charset="utf-8">
<title>Bright Harbor – Dental Care</title>
<link rel="stylesheet" href="https://fonts.googleapis.com/css2?family=Poppins:wght@400;500;600;700&family=Montserrat:wght@400;500;600;700&display=swap">
<style>
:root{
  --blue:#0094D4;--blue-2:#00A9DD;--blue-3:#6FCCEA;--blue-4:#C7EBF8;--blue-5:#E9F6FB;
  --green:#00AB8E;--green-2:#00BBA5;--green-3:#67D7C9;--green-4:#C6EFE9;--green-5:#E9F9F6;
  --ink:#3a3a3a;--text:#555;--navy:#0d3a57;--white:#fff;
}
*{box-sizing:border-box;margin:0;padding:0}
html,body{width:1200px;height:3955px;overflow:hidden}
body{position:relative;background:var(--blue-5);font-family:"Montserrat",sans-serif;color:var(--text)}
h1,h2,h3{font-family:"Poppins",sans-serif;font-weight:inherit}

/* header */
.site-header{position:absolute;left:0;top:0;width:1200px;height:107px;background:var(--white);box-shadow:0 1px 4px rgba(0,0,0,.08);z-index:3}
.brand{position:absolute;left:92px;top:38px;display:flex;align-items:center;gap:10px;font-family:"Poppins",sans-serif;font-weight:600;font-size:26px;color:var(--green)}
.brand i{width:16px;height:16px;border-radius:50%;background:var(--blue);display:block}
.main-nav a{position:absolute;top:63px;font-size:13.5px;color:#555;text-decoration:none;white-space:nowrap}
.main-nav .caret::after{content:"";display:inline-block;margin-left:5px;border:4px solid transparent;border-top-color:#999;transform:translateY(2px)}
.nav-active{position:absolute;left:313px;top:103px;width:78px;height:4px;background:var(--green)}
.top-phone{position:absolute;left:625px;top:10px;display:flex;align-items:center;gap:6px;color:var(--blue);font-weight:600;font-size:16px}
.top-btn{position:absolute;top:0;height:36px;width:152px;color:#fff;font-size:12.5px;font-weight:600;display:flex;align-items:center;justify-content:center}
.top-btn.schedule{left:793px;background:var(--blue-2)}
.top-btn.emergency{left:950px;background:var(--green-2)}

/* hero */
.hero{position:absolute;left:0;top:107px;width:1200px;height:570px;background:radial-gradient(ellipse at 55% 70%,#3fb7ec 0%,#0a9ad8 45%,#0180c4 100%);overflow:hidden}
.hero-wave{position:absolute;left:0;top:300px;width:1200px;height:220px;background:linear-gradient(180deg,rgba(255,255,255,0) 0%,rgba(160,225,250,.18) 50%,rgba(255,255,255,0) 100%)}
.hero-art{position:absolute;left:620px;top:80px;width:470px;height:400px;border-radius:40px;background:radial-gradient(ellipse at center,rgba(255,255,255,.18),rgba(255,255,255,0) 70%)}
.hero-copy{position:absolute;left:107px;top:138px;color:#fff}
.hero-copy .l1{display:block;font-size:50px;font-weight:400;line-height:50px}
.hero-copy .l2{display:block;font-size:50px;font-weight:700;line-height:52px}
.hero-copy p{margin-top:14px;font-family:"Poppins",sans-serif;font-size:22px;line-height:30px}
.btn-outline{position:absolute;left:101px;top:331px;width:237px;height:54px;border:2px solid #fff;border-radius:28px;color:#fff;font-size:13px;font-weight:700;display:flex;align-items:center;justify-content:center;letter-spacing:.3px}
.scroll-down{position:absolute;left:568px;top:643px;width:64px;height:64px;border-radius:50%;background:#fff;box-shadow:0 4px 12px rgba(0,0,0,.15);display:flex;align-items:center;justify-content:center;z-index:2}

/* team */
.team{position:absolute;left:0;top:677px;width:1200px;height:595px;background:#fff;border-bottom-left-radius:110px;overflow:hidden}
.section-title{font-family:"Poppins",sans-serif;font-weight:600;font-size:36px;color:var(--ink);text-align:center}
.team .section-title{position:absolute;top:75px;width:100%}
.team-badge{position:absolute;left:486px;top:176px;width:254px;height:77px;background:var(--green);color:#fff;text-align:center;font-family:"Poppins",sans-serif;padding-top:12px;box-shadow:0 4px 10px rgba(0,0,0,.12);z-index:1}
.team-badge b{display:block;font-size:19px;font-weight:600}
.team-badge span{font-size:16px}
.team-badge::after{content:"";position:absolute;left:118px;bottom:-9px;border:9px solid transparent;border-top-color:var(--green);border-bottom:0}
.portrait{position:absolute;top:283px;height:312px}
.portrait.side{background:linear-gradient(180deg,#f2f2f2,#d9d9d9)}
.portrait.main{background:linear-gradient(180deg,#e9e4e1 0%,#7a6a66 55%,#2a2d3a 100%)}
.team-arrow{position:absolute;top:362px}

/* bio */
.bio-name{position:absolute;left:127px;top:1350px;font-family:"Poppins",sans-serif;font-size:28px;font-weight:600;color:var(--ink)}
.bio-role{position:absolute;left:127px;top:1384px;font-family:"Poppins",sans-serif;font-size:21px;color:var(--blue)}
.bio-text{position:absolute;font-size:13px;line-height:23px;color:#555;text-align:justify}
.bio-text p+p{margin-top:15px}
.checklist{position:absolute;left:595px;top:1536px;list-style:none}
.checklist li{display:flex;align-items:center;gap:9px;font-size:12px;font-weight:500;color:#444;height:28px}

/* services */
.services{position:absolute;left:0;top:1750px;width:1200px;height:556px;background:#fff;border-top-right-radius:110px;border-bottom-left-radius:110px}
.services .section-title{position:absolute;top:38px;width:100%}
.title-rule{position:absolute;height:3px;background:var(--green)}
.service-card{position:absolute;width:224px;height:105px;border:1.5px solid var(--blue-4);background:#fff;display:flex;align-items:center;gap:14px;padding-left:24px;font-size:13.5px;font-weight:600;color:#3c5a6a;text-transform:uppercase;line-height:17px;box-shadow:0 2px 6px rgba(0,120,180,.06)}
.service-card svg{flex:0 0 auto}
.service-card.active{background:linear-gradient(135deg,#2aa6e6,#0a7fd0);border-color:transparent;color:#fff;box-shadow:0 6px 16px rgba(0,120,200,.3)}

/* experience */
.exp-photo{position:absolute;left:600px;top:2486px;width:400px;height:465px;z-index:0;background:radial-gradient(ellipse 55% 45% at 50% 32%,#8a5e48 0%,#6b4a3b 55%,rgba(107,74,59,0) 100%),linear-gradient(180deg,rgba(233,246,251,0) 0%,#dfe9ef 60%,#d3e2ea 100%)}
.exp-title{position:absolute;left:121px;top:2384px;font-family:"Poppins",sans-serif;font-size:34px;line-height:42px;font-weight:400;color:var(--ink);z-index:1}
.exp-title b{font-weight:600}
.exp-text{position:absolute;left:124px;top:2492px;width:452px;font-size:12.3px;line-height:16.5px;color:#555;z-index:1}
.exp-text p+p{margin-top:16px}
.review-card{position:absolute;left:789px;top:2377px;width:305px;height:451px;background:#fff;box-shadow:0 6px 20px rgba(0,80,130,.12);text-align:center;font-family:"Poppins",sans-serif;z-index:2}
.review-card .avg{position:absolute;top:33px;width:100%;font-size:14px;font-weight:600;color:#333;letter-spacing:.4px}
.stars{color:#f5b400;letter-spacing:2px}
.review-card .rating{position:absolute;top:58px;width:100%;font-size:16px}
.review-card .rating b{color:#333;font-size:15px;margin-left:6px}
.review-card .count{position:absolute;top:90px;width:100%;font-size:10.5px;color:#444;display:flex;justify-content:center;align-items:center;gap:6px}
.review-card .count i{width:16px;height:16px;border-radius:50%;background:var(--blue);display:block}
.platforms{position:absolute;top:137px;left:0;width:100%;display:flex;justify-content:center;gap:22px;font-size:12px;font-weight:500;color:#555}
.avatar{position:absolute;left:58px;top:185px;width:52px;height:52px;border-radius:50%;background:linear-gradient(135deg,#c9a48c,#7b5a4a)}
.review-card .rstars{position:absolute;left:122px;top:185px;font-size:15px}
.review-card .rname{position:absolute;left:122px;top:210px;font-size:14px;font-weight:600;color:#333}
.review-card .rtext{position:absolute;left:58px;top:262px;width:190px;text-align:left;font-family:"Montserrat",sans-serif;font-size:8.6px;line-height:11px;color:#444}
.review-card .rtext span{color:var(--blue)}
.review-card .rdate{position:absolute;left:58px;top:346px;font-size:9px;color:#888}
.review-card .rline{position:absolute;left:58px;top:372px;width:190px;height:1px;background:#eee}
.review-card .source{position:absolute;left:58px;top:396px;width:190px;display:flex;justify-content:space-between;align-items:center;font-size:9px;color:#555}
.review-card .source b{font-size:17px;font-weight:500;color:var(--blue)}
.rev-arrow{position:absolute;top:262px}

/* banner */
.banner{position:absolute;left:0;top:2951px;width:1200px;height:505px;background:linear-gradient(90deg,#1e5a78 0%,#143f58 55%,#0f3550 100%);overflow:hidden}
.banner-photo{position:absolute;left:0;top:0;width:720px;height:505px;background:linear-gradient(90deg,rgba(90,150,190,1) 0%,rgba(200,140,110,.9) 40%,rgba(225,110,50,.6) 60%,rgba(20,63,88,0) 100%)}
.banner-copy{position:absolute;left:623px;top:140px;color:#fff}
.banner-copy h2{font-size:38px;line-height:42px;font-weight:700}
.banner-copy h2 span{font-weight:400;display:block}
.banner-copy p{margin-top:14px;font-family:"Poppins",sans-serif;font-size:20px}
.btn-green{position:absolute;left:620px;top:290px;width:250px;height:54px;border-radius:28px;background:var(--green-2);color:#fff;font-size:13px;font-weight:700;display:flex;align-items:center;justify-content:center}

/* footer */
.site-footer{position:absolute;left:0;top:3456px;width:1200px;height:499px;background:var(--blue);color:#fff}
.f-head{position:absolute;top:56px;font-family:"Poppins",sans-serif;font-size:18px;font-weight:500}
.f-rule{position:absolute;top:88px;width:170px;height:1px;background:rgba(255,255,255,.45)}
.f-line{position:absolute;display:flex;gap:12px;font-size:12.5px;line-height:20px}
.hours{position:absolute;left:477px;top:118px;font-size:12.5px}
.hours div{display:flex;height:29.5px}
.hours span{width:115px}
.map{position:absolute;left:770px;top:112px;width:307px;height:184px;background:#eef1f3;border:2px solid #d4e6f1}
.btn-dark{position:absolute;left:144px;top:258px;width:206px;height:38px;border-radius:20px;background:var(--navy);color:#fff;font-size:12px;font-weight:700;display:flex;align-items:center;justify-content:center}
.f-divider{position:absolute;left:0;top:354px;width:1200px;height:1px;background:rgba(255,255,255,.3)}
.f-links a{position:absolute;top:386px;font-size:12px;color:#fff;text-decoration:none}
.socials{position:absolute;left:939px;top:380px;display:flex;gap:6px}
.socials i{width:24px;height:24px;border-radius:50%;background:#fff;display:block}
.copyright{position:absolute;left:147px;top:423px;font-size:10.5px}
</style>
</head>
<body>

<svg width="0" height="0" style="position:absolute">
  <symbol id="tooth" viewBox="0 0 48 48">
    <path d="M14 6c-6 0-9 5-9 11 0 6 3 9 4 15 1 6 2 11 6 11 3 0 3-8 5-12 1-2 2-3 4-3s3 1 4 3c2 4 2 12 5 12 4 0 5-5 6-11 1-6 4-9 4-15 0-6-3-11-9-11-4 0-6 2-10 2S18 6 14 6z" fill="none" stroke="currentColor" stroke-width="2.4" stroke-linejoin="round"/>
  </symbol>
  <symbol id="tick" viewBox="0 0 20 20">
    <circle cx="10" cy="10" r="8.5" fill="none" stroke="#00AB8E" stroke-width="1.6"/>
    <path d="M6 10.3l2.7 2.7L14 7.5" fill="none" stroke="#00AB8E" stroke-width="1.8" stroke-linecap="round" stroke-linejoin="round"/>
  </symbol>
</svg>

<header class="site-header">
  <div class="brand"><i></i>Bright Harbor</div>
  <nav class="main-nav">
    <a class="caret" style="left:316px">About Us</a>
    <a class="caret" style="left:413px">Services</a>
    <a style="left:505px">Financing</a>
    <a style="left:606px">Testimonials</a>
    <a style="left:723px">New Patient Visit</a>
    <a style="left:869px">Specials</a>
    <a style="left:961px">Contact Us</a>
    <a style="left:1070px">Blog</a>
  </nav>
  <div class="nav-active"></div>
  <div class="top-phone">
    <svg width="20" height="20" viewBox="0 0 20 20"><circle cx="10" cy="10" r="10" fill="#0094D4"/><path d="M7 5.5l1.6 2.3-1 1.1c.7 1.5 1.8 2.6 3.3 3.3l1.1-1 2.3 1.6-.8 1.7c-4 .1-7.5-3.4-7.4-7.4z" fill="#fff"/></svg>
    (714) 555-0148
  </div>
  <div class="top-btn schedule">Schedule Online</div>
  <div class="top-btn emergency">Emergency</div>
</header>

<section class="hero">
  <div class="hero-wave"></div>
  <div class="hero-art" role="img" aria-label="Large white line drawing of two teeth"></div>
  <div class="hero-copy">
    <h1><span class="l1">Creating</span><span class="l2">Healthier Smiles</span></h1>
    <p>With Advanced Technology and<br>Affordable Treatment</p>
  </div>
  <div class="btn-outline">BOOK AN APPOINTMENT</div>
</section>
<div class="scroll-down">
  <svg width="22" height="26" viewBox="0 0 22 26"><path d="M11 2v21M3 15l8 8 8-8" fill="none" stroke="#0094D4" stroke-width="2" stroke-linecap="round"/></svg>
</div>

<section class="team">
  <h2 class="section-title">Meet Our Team</h2>
  <div class="team-badge"><b>Dr. Anika Rao</b><span>Endodontist</span></div>
  <div class="portrait side" style="left:207px;width:238px" role="img" aria-label="Black and white portrait of a male dentist in a white coat"></div>
  <div class="portrait main" style="left:445px;width:270px" role="img" aria-label="Color portrait of the endodontist in a dark blazer"></div>
  <div class="portrait side" style="left:715px;width:267px" role="img" aria-label="Black and white portrait of a female dentist in a white coat"></div>
  <svg class="team-arrow" style="left:140px" width="24" height="44" viewBox="0 0 24 44"><path d="M21 2L3 22l18 20" fill="none" stroke="#6FCCEA" stroke-width="2.5"/></svg>
  <svg class="team-arrow" style="left:1050px;top:370px" width="24" height="44" viewBox="0 0 24 44"><path d="M3 2l18 20L3 42" fill="none" stroke="#6FCCEA" stroke-width="2.5"/></svg>
</section>

<h3 class="bio-name">Dr. Anika Rao</h3>
<div class="bio-role">Endodontist</div>
<div class="bio-text" style="left:127px;top:1432px;width:398px">
  <p>Dr. Rao received her specialty training in Endodontics from Westbrook University. She graduated with a Master of Science in dentistry degree, in endodontics. She has practiced in Southern California for many years as a general dentist before specializing in endodontics and uses her experience to help her patients make the right decisions, regarding their treatment plans. She is gentle, compassionate and is committed to providing the optimum care for her patients.</p>
  <p>Dr. Rao is a member of several professional and service organizations, including:</p>
</div>
<div class="bio-text" style="left:595px;top:1369px;width:461px;font-size:12.6px;line-height:19.5px">
  <p>Dr. Rao is an active member of the National Society of Endodontic Care and keeps herself updated with the latest methods and technologies in endodontics. In her free time, Dr. Rao enjoys cooking, travelling, and spending time with her family.</p>
  <p>Dr. Rao is a member of several professional and service organizations, including:</p>
</div>
<ul class="checklist">
  <li><svg width="20" height="20"><use href="#tick"/></svg>National Dental Guild (NDG)</li>
  <li><svg width="20" height="20"><use href="#tick"/></svg>Western State Dental Council (WSDC)</li>
  <li><svg width="20" height="20"><use href="#tick"/></svg>Global Dental Fellowship (GDF)</li>
  <li><svg width="20" height="20"><use href="#tick"/></svg>Bay County Dental Society (BCDS)</li>
</ul>

<section class="services">
  <h2 class="section-title">Our Services</h2>
  <div class="title-rule" style="left:568px;top:88px;width:64px"></div>

  <div class="service-card active" style="left:127px;top:125px"><svg width="40" height="40" style="color:#fff"><use href="#tooth"/></svg>Dental<br>Implants</div>
  <div class="service-card" style="left:364px;top:125px"><svg width="44" height="44" style="color:#00AB8E"><use href="#tooth"/></svg>Cosmetic<br>Dentistry</div>
  <div class="service-card" style="left:602px;top:125px"><svg width="44" height="44" style="color:#00AB8E"><use href="#tooth"/></svg>Braces</div>
  <div class="service-card" style="left:839px;top:125px"><svg width="40" height="40" style="color:#00AB8E"><use href="#tooth"/></svg>Crowns</div>

  <div class="service-card" style="left:127px;top:245px"><svg width="44" height="40" style="color:#00AB8E"><use href="#tooth"/></svg>Bridge</div>
  <div class="service-card" style="left:364px;top:245px"><svg width="44" height="44" style="color:#00AB8E"><use href="#tooth"/></svg>Extractions</div>
  <div class="service-card" style="left:602px;top:245px"><svg width="44" height="44" style="color:#00AB8E"><use href="#tooth"/></svg>Gum Disease</div>
  <div class="service-card" style="left:839px;top:245px"><svg width="44" height="44" style="color:#00AB8E"><use href="#tooth"/></svg>Root Canal</div>

  <div class="service-card" style="left:127px;top:366px"><svg width="44" height="44" style="color:#00AB8E"><use href="#tooth"/></svg>Dentures</div>
  <div class="service-card" style="left:364px;top:366px"><svg width="44" height="44" style="color:#00AB8E"><use href="#tooth"/></svg>Emergency<br>Dentistry</div>
  <div class="service-card" style="left:602px;top:366px"><svg width="44" height="44" style="color:#00AB8E"><use href="#tooth"/></svg>Veneers</div>
  <div class="service-card" style="left:839px;top:366px"><svg width="44" height="40" style="color:#00AB8E"><use href="#tooth"/></svg>Clear<br>Aligners</div>
</section>

<div class="exp-photo" role="img" aria-label="Smiling young man wearing glasses and a light denim shirt"></div>
<h2 class="exp-title"><b>Experience the Bright</b><br>Harbor Difference</h2>
<div class="title-rule" style="left:121px;top:2473px;width:56px"></div>
<div class="exp-text">
  <p>Your smile is our #1 priority. At Bright Harbor, we provide affordable and expert dental solutions. Whether you are looking for a family dentist or have any emergency such as needing a root canal in Lakeside, we are here for you! We want to keep your teeth healthy inside and out. We don't just clean teeth and send you on your way, we want to get to know you.</p>
  <p>We accept most HMO and PPO insurances. We offer various financing options through SmilePay Credit, LendWell and In-House Plans.</p>
  <p>To constantly strive to achieve the highest level of skills and modern techniques and equipment so we can provide our patients with the best that Dentistry has to offer at our dental office in Lakeside, Bay County, CA.</p>
  <p>We provide patients with the best experience you can find in all of Southern California. We provide a comfortable and friendly atmosphere to shatter any fears you may have. We supply you with all the information on your dental health options so you can feel comfortable in the choices you make, whether it's a routine check-up or dental implants in Lakeside.</p>
  <p>We are available for Emergency and Walk-ins.</p>
</div>

<aside class="review-card">
  <div class="avg">AVERAGE RATING</div>
  <div class="rating"><span class="stars">★★★★★</span><b>4.9</b></div>
  <div class="count"><i></i>126 Reviews</div>
  <div class="platforms"><span>ReviewHub</span><span>LocalStar</span><span>Circlebook</span></div>
  <div class="avatar" role="img" aria-label="Reviewer profile photo"></div>
  <div class="rstars stars">★★★★★</div>
  <div class="rname">Laura Bennett</div>
  <div class="rtext">Dr. Rao and her staff are wonderful! Everyone is so kind and welcoming. I always have a great visit. I never feel rushed and there is time to ask questions and make sure we are on the same page! This office i... <span>more</span></div>
  <div class="rdate">26 February, 2021</div>
  <div class="rline"></div>
  <div class="source"><span>Source:</span><b>ReviewHub</b></div>
  <svg class="rev-arrow" style="left:26px" width="10" height="16" viewBox="0 0 10 16"><path d="M8 2L2 8l6 6" fill="none" stroke="#0094D4" stroke-width="2"/></svg>
  <svg class="rev-arrow" style="left:269px" width="10" height="16" viewBox="0 0 10 16"><path d="M2 2l6 6-6 6" fill="none" stroke="#0094D4" stroke-width="2"/></svg>
</aside>

<section class="banner">
  <div class="banner-photo" role="img" aria-label="Dentist in blue gloves examining a smiling patient in an orange chair"></div>
  <div class="banner-copy">
    <h2>Committed to Excellence<span>in Oral Health Care</span></h2>
    <p>Free Exam and X-Rays for New Patients</p>
  </div>
  <div class="btn-green">BOOK AN APPOINTMENT</div>
</section>

<footer class="site-footer">
  <div class="f-head" style="left:144px">BRIGHT HARBOR</div>
  <div class="f-rule" style="left:144px"></div>
  <div class="f-head" style="left:477px">OFFICE HOURS</div>
  <div class="f-rule" style="left:477px"></div>
  <div class="f-head" style="left:766px">OUR LOCATION</div>
  <div class="f-rule" style="left:766px"></div>

  <div class="f-line" style="left:144px;top:114px">
    <svg width="18" height="22" viewBox="0 0 18 22"><path d="M9 1a7 7 0 0 0-7 7c0 5 7 13 7 13s7-8 7-13a7 7 0 0 0-7-7z" fill="#fff"/><circle cx="9" cy="8" r="2.6" fill="#0094D4"/></svg>
    <span>210 Harbor View Ave., Suite B<br>Lakeside, CA 90000</span>
  </div>
  <div class="f-line" style="left:144px;top:182px">
    <svg width="18" height="18" viewBox="0 0 20 20"><path d="M5 2l3 4-2 2c1 3 3 5 6 6l2-2 4 3-2 3C9 18 2 11 2 4z" fill="#fff"/></svg>
    <span>Call Us: (714) 555-0148</span>
  </div>
  <div class="f-line" style="left:144px;top:212px">
    <svg width="18" height="18" viewBox="0 0 20 20"><rect x="2" y="4" width="16" height="12" rx="1" fill="#fff"/><path d="M2 5l8 6 8-6" fill="none" stroke="#0094D4" stroke-width="1.4"/></svg>
    <span>hello@mybrightharbor.example</span>
  </div>
  <div class="btn-dark">BOOK AN APPOINTMENT</div>

  <div class="hours">
    <div><span>Monday:</span>10AM–7PM</div>
    <div><span>Tuesday:</span>10AM–7PM</div>
    <div><span>Wednesday:</span>9AM–6PM</div>
    <div><span>Thursday:</span>9AM–6PM</div>
    <div><span>Friday:</span>9AM–5PM</div>
    <div><span>Saturday:</span>9AM–1PM</div>
  </div>

  <div class="map" role="img" aria-label="Street map showing the office location with a pin"></div>

  <div class="f-divider"></div>
  <nav class="f-links">
    <a style="left:147px">About Us</a>
    <a style="left:234px">Services</a>
    <a style="left:317px">Financing</a>
    <a style="left:407px">Testimonials</a>
    <a style="left:511px">New Patient Visit</a>
    <a style="left:643px">Specials</a>
    <a style="left:725px">Contact Us</a>
    <a style="left:822px">Blog</a>
  </nav>
  <div class="socials"><i></i><i></i><i></i><i></i><i></i></div>
  <div class="copyright">2021 Bright Harbor &nbsp;|&nbsp; All Rights Reserved</div>
</footer>

</body>
</html>
```